MRT Property - Business Cards

Looking for a business card & general letterhead, signage etc design for our new logo.

Colours:
000a20
0056a2
00b5ef
0088ce
68cef2

Fonts:
Poppins
Karla

Please keep look and feel of new brand - example in the zip package I sent.

```html
<!DOCTYPE html>
<html lang="en">
<head>
<meta charset="utf-8">
<title>MRT Property – Business Cards</title>
<link href="https://fonts.googleapis.com/css2?family=Poppins:wght@400;500;600;700&display=swap" rel="stylesheet">
<style>
  :root {
    --stage: #222222;
    --navy: #10152a;
    --deep-blue: #0056a2;
    --mid-blue: #0088ce;
    --sky-blue: #00b5ef;
    --light-blue: #68cef2;
    --pattern-blue: #0d4f9c;
    --white: #ffffff;
  }
  * { box-sizing: border-box; margin: 0; padding: 0; }
  html, body {
    width: 1200px; height: 711px; overflow: hidden;
    background: var(--stage);
    font-family: "Poppins", sans-serif;
  }
  .stage {
    position: relative; width: 1200px; height: 711px;
    display: flex; align-items: center; justify-content: center; gap: 40px;
  }
  .card {
    position: relative; width: 540px; height: 309px;
    border-radius: 18px; overflow: hidden;
    border: 3px solid var(--light-blue);
  }
  /* Back */
  .card-back { background: var(--deep-blue); }
  .back-pattern {
    position: absolute; inset: 0;
    background: linear-gradient(135deg, var(--deep-blue), var(--pattern-blue));
  }
  .back-brand {
    position: absolute; right: 60px; top: 140px;
    color: var(--white); font-weight: 600; font-size: 15px; letter-spacing: 0.5px;
  }
  /* Front */
  .card-front { background: var(--navy); }
  .front-waves { position: absolute; inset: 0; }
  .front-brand {
    position: absolute; left: 32px; top: 38px;
    color: var(--deep-blue); font-weight: 700; font-size: 34px; line-height: 1;
    letter-spacing: 0.5px;
  }
  .holder {
    position: absolute; right: 40px; top: 26px; text-align: right;
  }
  .holder-name { font-size: 26px; line-height: 1.1; }
  .holder-first { color: var(--deep-blue); font-weight: 700; }
  .holder-last { color: var(--light-blue); font-weight: 400; }
  .holder-role { color: var(--white); font-size: 12px; font-weight: 500; }
  .edge-bar {
    position: absolute; right: 0; top: 22px; width: 16px; height: 48px;
    background: var(--deep-blue);
  }
  .address {
    position: absolute; left: 40px; top: 118px;
    color: var(--white); font-size: 12px; line-height: 1.45;
  }
  .contacts {
    position: absolute; left: 40px; top: 186px; list-style: none;
    color: var(--white); font-size: 12px; line-height: 1.5;
  }
  .contacts li { display: flex; align-items: center; gap: 8px; }
  .contacts svg { width: 11px; height: 11px; fill: var(--mid-blue); flex: none; }
</style>
</head>
<body>
<main class="stage">
  <section class="card card-back">
    <div class="back-pattern" role="img" aria-label="Repeating brand symbol pattern in blue tones"></div>
    <span class="back-brand">MRT Property</span>
  </section>

  <section class="card card-front">
    <svg class="front-waves" viewBox="0 0 540 309" preserveAspectRatio="none" aria-hidden="true">
      <path d="M0,285 C150,305 280,265 335,200 C385,140 440,128 540,118 L540,309 L0,309 Z" fill="var(--deep-blue)"/>
      <path d="M30,262 C160,292 285,262 372,208 C295,280 150,296 30,272 Z" fill="var(--light-blue)"/>
    </svg>
    <div class="edge-bar"></div>
    <h1 class="front-brand">MRT Property</h1>
    <div class="holder">
      <p class="holder-name"><span class="holder-first">Callum</span> <span class="holder-last">Reid</span></p>
      <p class="holder-role">Director</p>
    </div>
    <address class="address" style="font-style:normal">
      Suite 4.12, Level 4<br>
      18 Harbourline Road<br>
      Riverside Park NSW 2190
    </address>
    <ul class="contacts">
      <li><svg viewBox="0 0 24 24"><path d="M6.6 10.8a15.1 15.1 0 0 0 6.6 6.6l2.2-2.2a1 1 0 0 1 1-.25 11.4 11.4 0 0 0 3.6.57 1 1 0 0 1 1 1V20a1 1 0 0 1-1 1A17 17 0 0 1 3 4a1 1 0 0 1 1-1h3.5a1 1 0 0 1 1 1c0 1.25.2 2.45.57 3.57a1 1 0 0 1-.25 1z"/></svg>+61 2 9000 4182</li>
      <li><svg viewBox="0 0 24 24"><circle cx="12" cy="12" r="10"/></svg>www.mrtproperty.com.au</li>
      <li><svg viewBox="0 0 24 24"><path d="M2 5h20v14H2z"/></svg>hello@mrtproperty.com.au</li>
    </ul>
  </section>
</main>
</body>
</html>
```